Coral Reach Yachting Flyer

Coral Reach Yachting (.com) is a high end luxury and private charter company in the Cayman Islands. All info can be found on our webiste. I currently have a 4 panel roll fold flyer (Can supply working file). I am looking for a new fresh look but also need some changes as we have changes some boats, added some new charter ideas etc.

Between our website and current flyer I think the designer will get the idea. I Welcome new and fresh, I do not need it to match current website, as I may get that changed to.

We are looking for high end and simple/clean and comunicate reliability and professional with a hint of fun in the sun of course. Not whacky and tacky!!

The current PDF's of the current flyer needs a fair bit of changing (For example scuba diving panel will come out and go into a new 1 panel flyer.) I will need 3-4 other flyers too, and a bunch of other stuff in future for new businesses, but starting with this one so I can pick a designer (This is my 1st go with pixel bazaar, always did my own work, but am too busy and am not very good with creativity)

I have logo, support pictures, etc. Have uploaded the basics can email more info and changes after I find a designer. Lots of our boat pictures can be found at http://coralreachyachting.example/downloads/maple.zip

Also, we want a panel dedicated to wavedart.example as our big boat now has one onboard and our smaller boat (23') will have two and that will be a dedicated panel (Replace scuba) offering a "Wavedart Ultra Reef trip" (I will supply more info on that, once I pick a designer).

Target Market(s)

High end groups. The groups or families that will spend more to get more!!

Industry/Entity Type

It Company

```html
<!DOCTYPE html>
<html lang="en">
<head>
<meta charset="utf-8">
<title>Coral Reach Yachting – Roll Fold Flyer</title>
<link rel="stylesheet" href="https://fonts.googleapis.com/css2?family=Cinzel:wght@400;700&family=Arimo:wght@400;700&display=swap">
<style>
:root{
  --bg:#e9e6e1;
  --navy:#15283b;
  --ink:#2a2f35;
  --grey:#5b6167;
  --orange:#e8632a;
  --amber:#f0a21f;
  --gold:#e9b42a;
  --red:#d3202a;
  --white:#ffffff;
  --aqua-light:#c6edf4;
  --aqua:#7fd0e2;
  --teal:#1aa3b3;
  --teal-deep:#0d6f80;
  --sky:#a9d8ee;
}
*{box-sizing:border-box;margin:0;padding:0}
html,body{width:1200px;height:701px;overflow:hidden;background:var(--bg)}
.flyer{position:absolute;left:70px;top:14px;width:1060px;height:672px;display:flex;box-shadow:0 4px 14px rgba(0,0,0,.18)}
.panel{position:relative;width:265px;height:672px;overflow:hidden;font-family:"Arimo",Arial,sans-serif}
.photo{position:absolute}
.display{font-family:"Cinzel",Georgia,serif;font-weight:400;letter-spacing:.5px}
.heart{color:var(--red)}
.framed{border:3px solid var(--amber);border-radius:14px 3px 14px 3px;box-shadow:0 2px 5px rgba(0,0,0,.3)}
.framed-white{border:3px solid var(--white);border-radius:14px 3px 14px 3px;box-shadow:0 2px 5px rgba(0,0,0,.3)}

/* Panel 1 – boats */
.panel-boats{background:linear-gradient(180deg,var(--aqua-light),var(--aqua) 60%,#5fc2d8)}
.panel-boats .tagline{position:absolute;top:40px;width:100%;text-align:center;font-size:16px;color:var(--navy)}
.panel-boats .title{position:absolute;top:82px;left:26px;font-size:30px;color:var(--orange)}
.boat-list{position:absolute;top:138px;left:26px;list-style:none}
.boat-list li{font-weight:700;font-size:17px;color:var(--navy);line-height:28.5px}
.boat-list li::before{content:"\2022";color:var(--orange);margin-right:10px}
.thumb{width:104px;height:64px;background:linear-gradient(180deg,var(--sky),#e9f4f7 45%,var(--teal))}
.address-band{position:absolute;bottom:0;left:0;width:100%;height:56px;background:var(--orange);border-top:3px solid var(--white);color:var(--white);font-weight:700;font-size:13.5px;text-align:center;padding-top:9px;line-height:19px}

/* Panel 2 – why choose */
.panel-why{background:var(--white)}
.panel-why .title{position:absolute;top:24px;left:18px;font-size:26px;color:var(--orange)}
.intro{position:absolute;top:64px;left:18px;width:232px;font-size:9.6px;line-height:12.2px;color:var(--grey);font-weight:700;text-align:justify}
.sea{left:0;top:148px;width:265px;height:438px;background:linear-gradient(180deg,#eef7fa,#bde5ee 18%,var(--teal) 50%,var(--teal-deep))}
.inset{left:33px;top:228px;width:216px;height:96px;background:linear-gradient(180deg,var(--sky),#dbeff4 55%,#e8d9bd)}
.things-title{position:absolute;top:372px;left:28px;color:var(--white);font-weight:700;font-size:14.5px;line-height:18px}
.things{position:absolute;top:412px;left:28px;list-style:none}
.things li{color:var(--white);font-size:12.5px;line-height:18.2px}
.things li::before{content:"\2605";color:var(--amber);margin-right:7px}
.strip{position:absolute;left:0;bottom:0;width:265px;height:86px;display:flex;gap:2px;background:var(--white);padding:2px 0 0}
.strip div{flex:1;background:linear-gradient(180deg,var(--sky),#d9ecef 55%,#2f9fb2)}

/* Panel 3 – wavedart */
.panel-wavedart{background:var(--white)}
.collage{left:36px;top:16px;width:200px;height:192px;border-radius:34px 6px 34px 6px;background:linear-gradient(135deg,#8dc7d6,#e3d8c8 45%,#3bb0c0)}
.banner{position:absolute;left:0;top:226px;width:265px;height:70px;background:linear-gradient(180deg,#f7f9fa,#d7e8ee);padding:8px 0 0 20px;font-size:20px;line-height:24px;color:var(--orange)}
.action{left:0;top:296px;width:265px;height:98px;background:linear-gradient(180deg,#c9e3ea,#7fc0cf 55%,#4d9fb1)}
.body-copy{position:absolute;top:410px;left:20px;width:228px;font-size:9.4px;line-height:12.2px;color:var(--ink)}
.body-copy p{margin-bottom:8px}
.email-band{position:absolute;left:0;bottom:34px;width:100%;height:24px;background:var(--orange);color:var(--white);font-weight:700;font-size:12px;line-height:24px;padding-left:20px}
.web-band{position:absolute;left:0;bottom:0;width:100%;height:30px;background:var(--gold);color:var(--white);font-weight:700;font-size:12.5px;line-height:30px;padding-left:20px}

/* Panel 4 – cover */
.panel-cover{background:var(--white)}
.cover-photo{left:0;top:0;width:265px;height:500px;background:linear-gradient(180deg,#cfeaf7,#9fd3ea 20%,#e9f2f4 36%,var(--teal) 55%,#46bac7 80%,#f3f6f7)}
.call{position:absolute;top:12px;width:100%;text-align:center;color:var(--navy)}
.call .label{font-size:23px}
.call .phone{font-weight:700;font-size:15px;margin-top:4px}
.mini{width:78px;height:52px;background:linear-gradient(180deg,var(--sky),#eef5f6 50%,#d8c5a3)}
.cover-tag{position:absolute;top:488px;width:100%;text-align:center;font-size:16px;color:var(--navy)}
.brand{position:absolute;top:560px;width:100%;display:flex;align-items:center;justify-content:center;gap:8px}
.brand-name{font-family:"Cinzel",Georgia,serif;font-weight:700;font-size:17px;color:var(--navy)}
</style>
</head>
<body>
<main class="flyer">

  <section class="panel panel-boats">
    <p class="tagline display">SHOW YOUR <span class="heart">&#9829;</span> WITH US</p>
    <h2 class="title display">OUR BOATS</h2>
    <ul class="boat-list">
      <li>Lagoon Voyager</li>
      <li>Sunray Voyager</li>
      <li>Reef Voyager</li>
      <li>Horizon Voyager</li>
      <li>Tidewater Voyager</li>
      <li>Angler Voyager</li>
    </ul>
    <div class="photo thumb framed" style="left:20px;top:358px" role="img" aria-label="White motor yacht at sea"></div>
    <div class="photo thumb framed" style="left:142px;top:364px;height:56px" role="img" aria-label="Speedboat cruising"></div>
    <div class="photo thumb framed" style="left:30px;top:450px" role="img" aria-label="Boat on turquoise water"></div>
    <div class="photo thumb framed" style="left:146px;top:444px;height:68px" role="img" aria-label="Sport boat with bimini top"></div>
    <div class="photo thumb framed" style="left:20px;top:530px;height:68px" role="img" aria-label="Boat deck with seating"></div>
    <div class="photo thumb framed" style="left:142px;top:536px;height:60px" role="img" aria-label="Yacht anchored offshore"></div>
    <div class="address-band">18 Harbour Light Drive<br>Grand Cayman Cayman Islands</div>
  </section>

  <section class="panel panel-why">
    <h2 class="title display">WHY CHOOSE US?</h2>
    <p class="intro">We are a Caymanian owned company striving to offer something different to locals and tourists alike. For the past 30 years the founder of this company has enjoyed the unparalleled beauty of the Cayman Islands &amp; surrounding waters. Water skiing, diving, Rum Point...</p>
    <div class="photo sea" role="img" aria-label="Boat bow over turquoise sea"></div>
    <div class="photo inset framed" role="img" aria-label="Couple holding starfish on the beach"></div>
    <h3 class="things-title">THINGS TO DO WITH US<br>IN GRAND CAYMAN</h3>
    <ul class="things">
      <li>Swimming and Snorkeling</li>
      <li>Bioluminescence Night Diving</li>
      <li>SS Wayfarer Snorkeling</li>
      <li>Deep Sea Fishing</li>
      <li>Starfish Point</li>
      <li>Harbourside Bbq Tuesdays</li>
      <li>Purchase a vacation home</li>
      <li>Family Beach Portraits</li>
      <li>Rent your own vacation villa</li>
    </ul>
    <div class="strip">
      <div role="img" aria-label="Jumping into the sea"></div>
      <div role="img" aria-label="Family on the beach"></div>
      <div role="img" aria-label="Child on a rope swing"></div>
      <div role="img" aria-label="Jet ski on the water"></div>
      <div role="img" aria-label="Guest relaxing aboard"></div>
    </div>
  </section>

  <section class="panel panel-wavedart">
    <div class="photo collage" role="img" aria-label="Collage of guests snorkeling and riding underwater scooters"></div>
    <h2 class="banner display">Wavedart Ultra<br>Reef trip</h2>
    <div class="photo action" role="img" aria-label="Guests in the water with underwater scooters"></div>
    <div class="body-copy">
      <p>Lots of New Toys aboard Lagoon Voyager</p>
      <p>From the exciting Wavedart, leaping off the top deck, swinging on the rope swing, cruising with the jetski, relaxing in the Hammock or fishing in the gorgeous North Sound.</p>
      <p>You are guaranteed to have an incredible time with friends and family aboard Lagoon Voyager.</p>
      <p>Compliment your trip with our gourmet catering menu, on board cash bar, including local and international beer, wines, spirits and local rum punch.</p>
      <p>PRE-BOOK any of our extras while onboard Lagoon Voyager.</p>
    </div>
    <div class="email-band">info@CoralReachYachting.example</div>
    <div class="web-band">www.coralreachyachting.example</div>
  </section>

  <section class="panel panel-cover">
    <div class="photo cover-photo" role="img" aria-label="White sport boat speeding across turquoise water"></div>
    <div class="call">
      <p class="label display">CALL US NOW</p>
      <p class="phone">(345) 555-0148</p>
    </div>
    <div class="photo mini framed-white" style="left:58px;top:318px;height:48px" role="img" aria-label="Boat at anchor"></div>
    <div class="photo mini framed-white" style="left:150px;top:300px;width:100px;height:66px" role="img" aria-label="Guest on a sandbar"></div>
    <div class="photo mini framed-white" style="left:28px;top:382px;width:96px;height:66px" role="img" aria-label="Couple with starfish"></div>
    <div class="photo mini framed-white" style="left:150px;top:384px" role="img" aria-label="Underwater swim"></div>
    <p class="cover-tag display">SHOW YOUR <span class="heart">&#9829;</span> WITH US</p>
    <div class="brand">
      <svg width="22" height="22" viewBox="0 0 22 22" aria-hidden="true"><circle cx="11" cy="11" r="10" fill="var(--orange)"/></svg>
      <span class="brand-name">Coral Reach Yachting</span>
    </div>
  </section>

</main>
</body>
</html>
```